Corvane Lending Partners. Professional and Established Company

A full service finance company specializing in obtaining capital for small business. Business Lending advisor, helping small business owners access the capital they need to launch, grow, or sustain their business. Many of our programs offer flexible guidelines to overcome common obstacles such as credit score, credit history, and time in business, financials, and industry type. Our streamlined funding process makes getting a business loan, business line of credit, stated income commercial real estate loan, a smooth and stress free experience.SOME OF THE MOST COMMON NEEDS FOR BUSINESS CAPITAL:• Working Capital• Debt Consolidations (loans, merchant cash advances, etc.)• Payroll• Operating Expenses• Inventory• Equipment Financing• Commercial Real Estate (Purchase, Fix & Flip, Rehab, Renovations)• Business Acquisitions• Business ExpansionWe like the websites:www.quillmorecf.com they are in the same industry and provide the same servicesWe are wanting to be able to update when we do press releases and such using Word Press. Our look should be very professional and we will be adding Our Team Professional Bios and Headshots.

Industry/Entity Type

Finance

Number of Pages Required

5+ page

Font styles to use
Serif
Sans Serif

Requirements
Must have
• We want to copy quillmorecf.com
• We need:
• Home Page
• About Us
• Loan Programs
• Loan Criteria
• News
• Apply Now
• Contact
Nice to have
• See quillmorecf.com
Should not have
• Need professional design. Nothing bright or abstract

```html
<!DOCTYPE html>
<html lang="en">
<head>
<meta charset="utf-8">
<title>Corvane Lending Partners</title>
<link rel="stylesheet" href="https://fonts.googleapis.com/css2?family=Cinzel:wght@400;600;700&family=Open+Sans:wght@400;600;700&family=PT+Sans+Narrow:wght@700&display=swap">
<style>
:root{
  --blue:#2b6cb3;
  --blue-dark:#1e5595;
  --nav:#2f74bd;
  --grey:#7b7b7b;
  --ink:#1a1a1a;
  --text:#444;
  --white:#fff;
  --dark:#2d2d2d;
  --footer:#2f74bd;
}
*{box-sizing:border-box;margin:0;padding:0}
html,body{width:1200px;height:2885px;overflow:hidden;background:var(--white)}
body{position:relative;font-family:"Open Sans",Arial,sans-serif;color:var(--text)}
.abs{position:absolute}
.serif{font-family:"Cinzel",Georgia,serif}

/* header */
.header{left:0;top:0;width:1200px;height:92px;background:var(--white)}
.brand{left:144px;top:18px;font-family:"Cinzel",Georgia,serif;font-weight:700;color:var(--blue);font-size:27px;line-height:28px;letter-spacing:1px}
.brand small{display:block;font-size:13px;letter-spacing:3px;line-height:20px}
.contact-item{top:24px;display:flex;gap:14px;align-items:center}
.contact-item .ico{width:34px;height:34px;border:1px solid #ddd;transform:rotate(45deg);display:flex;align-items:center;justify-content:center}
.contact-item .ico svg{transform:rotate(-45deg)}
.contact-item .lbl{font-size:13px;color:var(--blue);line-height:18px}
.contact-item .val{font-size:13px;color:#333;line-height:20px}
.quote-btn{left:946px;top:28px;width:112px;height:36px;background:var(--grey);color:var(--white);font-weight:700;font-size:12px;display:flex;align-items:center;justify-content:center;letter-spacing:.5px}

/* nav */
.nav{left:0;top:92px;width:1200px;height:43px;background:var(--nav)}
.nav a{position:absolute;top:0;height:43px;line-height:43px;color:var(--white);font-size:13px;text-decoration:none;transform:translateX(-50%)}
.nav a.active{background:var(--grey);width:100px;text-align:center;font-weight:700}

/* hero */
.hero{left:0;top:135px;width:1200px;height:534px;background:linear-gradient(180deg,#7e9cc0 0%,#4c6f98 45%,#243a58 100%)}
.hero h1{position:absolute;left:0;width:1200px;top:190px;text-align:center;font-family:"PT Sans Narrow",Arial,sans-serif;font-weight:700;color:var(--white);font-size:35px;line-height:46px;letter-spacing:.5px}
.hero .btn{left:518px;top:317px;width:163px;height:36px;background:var(--blue);border:1px solid #8fb6e0;color:var(--white);font-size:13px;font-weight:700;display:flex;align-items:center;justify-content:center}
.hero .arrow{top:252px;width:32px;height:32px;border:1px solid rgba(255,255,255,.7);border-radius:50%}

/* about */
.section-title{left:0;width:1200px;text-align:center;font-family:"Cinzel",Georgia,serif}
.about-title{top:738px;color:var(--blue);font-size:32px;font-weight:400}
.about-lead{left:0;width:1200px;top:806px;text-align:center;color:var(--blue);font-weight:700;font-size:15.5px}
.about-text{left:180px;width:840px;top:838px;text-align:center;font-size:13px;line-height:22px;color:#555}
.btn-small{left:543px;top:950px;width:114px;height:33px;background:var(--blue);color:var(--white);font-family:"Cinzel",Georgia,serif;font-size:13px;display:flex;align-items:center;justify-content:center}

.news-title{top:1050px;color:var(--ink);font-size:34px;font-weight:600}
.news-panel{background:linear-gradient(90deg,#1f5ea6,#3a7cc4);color:var(--white);padding:40px 0 0}
.news-panel h3{font-family:"Cinzel",Georgia,serif;font-weight:600;font-size:22px;line-height:30px;letter-spacing:.3px}
.news-panel p{font-size:12.5px;line-height:22px;margin-top:10px;color:#e6eef8}
.news-panel .more{font-weight:700;font-size:15px;margin-top:10px;display:block}
.photo-a{background:linear-gradient(160deg,#cfe0f1,#5a86b6 55%,#294d7a)}
.photo-b{background:linear-gradient(180deg,#1c3050,#3d6ea6 60%,#b98a4d)}

/* loans */
.loans-title{top:1748px;color:var(--blue);font-size:32px}
.loan{width:300px;display:flex;gap:16px}
.loan svg{flex:none}
.loan h4{font-family:"Cinzel",Georgia,serif;font-weight:400;font-size:14px;color:#222;margin-top:2px}
.loan p{font-size:13px;line-height:19px;color:#444;margin-top:2px}

/* contact */
.contact{left:0;top:2227px;width:1200px;height:408px;background:linear-gradient(90deg,#4a4a4a,#2c2c2c 60%,#1a1a1a)}
.contact-title{top:2292px;color:var(--white);font-size:32px}
.contact-brand{left:144px;top:2362px;font-family:"Cinzel",Georgia,serif;font-weight:400;color:#cfcfcf;font-size:30px;line-height:32px}
.contact-brand small{display:block;font-size:15px;letter-spacing:3px}
.info{left:144px;color:var(--white);font-size:13px;display:flex;gap:14px;align-items:flex-start}
.info b{display:block;font-size:13px}
.field{left:775px;width:273px;height:31px;border:1px solid #aaa;color:#ddd;font-size:12px;padding:6px 6px;background:rgba(0,0,0,.15)}
.submit{left:775px;top:2547px;width:108px;height:33px;background:var(--blue);color:var(--white);font-family:"Cinzel",Georgia,serif;font-size:16px;display:flex;align-items:center;justify-content:center;border:1px solid #9cc0e6}

.map{left:0;top:2635px;width:1200px;height:207px;background:linear-gradient(135deg,#e2e2e2,#cfcfcf 60%,#dadada)}
.map-tag{left:453px;top:2713px;background:var(--white);padding:6px 10px;font-family:"Cinzel",Georgia,serif;font-weight:700;color:var(--blue);font-size:14px}

.footer{left:0;top:2842px;width:1200px;height:43px;background:var(--footer);color:var(--white);font-size:12.5px}
.footer span{position:absolute;left:144px;top:13px}
.social{position:absolute;top:11px;width:21px;height:21px;border-radius:50%;border:1.5px solid var(--white)}
</style>
</head>
<body>

<header class="abs header">
  <div class="abs brand">Corvane<small>Lending Partners</small></div>
  <div class="abs contact-item" style="left:502px">
    <div class="ico"><svg width="14" height="14" viewBox="0 0 24 24"><path d="M6 2l4 4-2 3c1 3 4 6 7 7l3-2 4 4-3 4C10 22 2 14 2 5z" fill="#2b6cb3"/></svg></div>
    <div><div class="lbl">Call Us</div><div class="val">(00) 123 456 7890</div></div>
  </div>
  <div class="abs contact-item" style="left:670px">
    <div class="ico"><svg width="14" height="12" viewBox="0 0 24 18"><rect x="1" y="1" width="22" height="16" fill="#2b6cb3"/><path d="M1 1l11 9 11-9" stroke="#fff" stroke-width="2" fill="none"/></svg></div>
    <div><div class="lbl">Email On</div><div class="val">inquiry@corvanelending.com</div></div>
  </div>
  <div class="abs quote-btn">GET A QUOTE</div>
</header>

<nav class="abs nav">
  <a class="active" href="#" style="left:191px">HOME</a>
  <a href="#" style="left:329px">ABOUT US</a>
  <a href="#" style="left:473px">LOAN PROGRAMS</a>
  <a href="#" style="left:633px">LOAN CRITERIA</a>
  <a href="#" style="left:756px">NEWS</a>
  <a href="#" style="left:871px">APPLY NOW</a>
  <a href="#" style="left:1006px">CONTACT US</a>
</nav>

<section class="abs hero" role="img" aria-label="Glass skyscrapers seen from below against a blue sky">
  <h1>WE ARE FULL SERVICE FINANCE COMPANY<br>SPECIALIZING IN OBTAINING CAPITAL<br>FOR SMALL BUSINESS.</h1>
  <div class="abs btn">CONTACT US TODAY</div>
  <div class="abs arrow" style="left:53px"><svg width="30" height="30"><path d="M17 10l-5 5 5 5" stroke="#fff" fill="none" stroke-width="1.5"/></svg></div>
  <div class="abs arrow" style="left:1115px"><svg width="30" height="30"><path d="M13 10l5 5-5 5" stroke="#fff" fill="none" stroke-width="1.5"/></svg></div>
</section>

<h2 class="abs section-title about-title">About Corvane</h2>
<p class="abs about-lead">Nullam euismod, augue at fermentum sodales, augue elit sagittis metus, eu sagittis ex nisl sed magna.</p>
<p class="abs about-text">Lorem ipsum dolor sit amet, consectetur adipiscing elit, sed do eiusmod tempor incididunt ut labore et dolore magna aliqua. Ut enim ad minim veniam, quis nostrud exercitation ullamco laboris nisi ut aliquip ex ea commodo consequat. Duis aute irure dolor in reprehenderit in voluptate velit esse cillum dolore eu fugiat nulla pariatur. Excepteur sint occaecat cupidatat non proident, sunt in culpa qui officia deserunt purus nec commodo consectetur, velit ligula laoreet tellus, ut vestibulum orci mollit anim id est laborum</p>
<div class="abs btn-small">Read More</div>

<h2 class="abs section-title news-title">LATEST NEWS</h2>

<article class="abs news-panel" style="left:0;top:1123px;width:811px;height:281px;padding-left:144px;padding-right:30px">
  <h3>Proin euismod, est mollis tempor convallis, massa ipsum semper ex, at mattis sem velit mattis arcu.</h3>
  <p>Etiam lacinia ullamcorper sapien, ut sollicitudin metus maximus a. Aliquam ut nulla eu urna luctus tincidunt. In at sodales est, sed porta purus. Integer ac neque id ante lacinia consequat dapibus vel est. Morbi accumsan tellus a volutpat venenatis. Phasellus volutpat odio nec libero elementum pretium. Etiam laoreet eros tellus, at pretium eros consectetur ac. Nunc at condimentum eros, eget mattis ipsum.</p>
  <span class="more">Read More....</span>
</article>
<div class="abs photo-a" style="left:811px;top:1123px;width:389px;height:281px" role="img" aria-label="Modern glass office towers under a cloudy sky"></div>

<div class="abs photo-b" style="left:0;top:1404px;width:388px;height:283px" role="img" aria-label="Illuminated apartment buildings at dusk"></div>
<article class="abs news-panel" style="left:388px;top:1404px;width:812px;height:283px;padding-left:38px;padding-right:144px">
  <h3>Proin euismod, est mollis tempor convallis, massa ipsum semper ex, at mattis sem velit mattis arcu.</h3>
  <p>Etiam lacinia ullamcorper sapien, ut sollicitudin metus maximus a. Aliquam ut nulla eu urna luctus tincidunt. In at sodales est, sed porta purus. Integer ac neque id ante lacinia consequat dapibus vel est. Morbi accumsan tellus a volutpat venenatis. Phasellus volutpat odio nec libero elementum pretium. Etiam laoreet eros tellus, at pretium eros consectetur ac. Nunc at condimentum eros, eget mattis ipsum.</p>
  <span class="more">Read More....</span>
</article>

<h2 class="abs section-title loans-title">LOAN PROGRAMS</h2>

<div class="abs loan" style="left:148px;top:1826px"><svg width="66" height="66"><circle cx="33" cy="33" r="32" fill="#2b6cb3"/><circle cx="33" cy="33" r="28" fill="none" stroke="#fff" stroke-width="1"/><rect x="20" y="25" width="26" height="16" fill="none" stroke="#fff" stroke-width="2"/></svg><div><h4>Working Capital</h4><p>Sed a pulvinar sapien. Aenean eleifend eget velit quis malesuada.</p></div></div>
<div class="abs loan" style="left:460px;top:1826px"><svg width="66" height="66"><circle cx="33" cy="33" r="32" fill="#2b6cb3"/><circle cx="33" cy="33" r="28" fill="none" stroke="#fff" stroke-width="1"/><path d="M33 18v28M21 26h24M21 26l-4 10h8zM45 26l-4 10h8z" stroke="#fff" stroke-width="2" fill="none"/></svg><div><h4>Debt Consolidations</h4><p>Sed a pulvinar sapien. Aenean eleifend eget velit quis malesuada.</p></div></div>
<div class="abs loan" style="left:773px;top:1826px"><svg width="66" height="66"><circle cx="33" cy="33" r="32" fill="#2b6cb3"/><circle cx="33" cy="33" r="28" fill="none" stroke="#fff" stroke-width="1"/><rect x="22" y="22" width="22" height="14" fill="#fff"/><path d="M18 42h30" stroke="#fff" stroke-width="3"/></svg><div><h4>Payroll</h4><p>Sed a pulvinar sapien. Aenean eleifend eget velit quis malesuada.</p></div></div>

<div class="abs loan" style="left:148px;top:1948px"><svg width="66" height="66"><circle cx="33" cy="33" r="32" fill="#2b6cb3"/><circle cx="33" cy="33" r="28" fill="none" stroke="#fff" stroke-width="1"/><rect x="19" y="24" width="28" height="18" rx="2" fill="none" stroke="#fff" stroke-width="2"/><path d="M19 30h28" stroke="#fff" stroke-width="3"/></svg><div><h4>Operating Expenses</h4><p>Sed a pulvinar sapien. Aenean eleifend eget velit quis malesuada.</p></div></div>
<div class="abs loan" style="left:460px;top:1948px"><svg width="66" height="66"><circle cx="33" cy="33" r="32" fill="#2b6cb3"/><circle cx="33" cy="33" r="28" fill="none" stroke="#fff" stroke-width="1"/><rect x="22" y="19" width="22" height="28" fill="none" stroke="#fff" stroke-width="2"/><path d="M26 27h14M26 33h14M26 39h10" stroke="#fff" stroke-width="2"/></svg><div><h4>Inventory</h4><p>Sed a pulvinar sapien. Aenean eleifend eget velit quis malesuada.</p></div></div>
<div class="abs loan" style="left:773px;top:1948px"><svg width="66" height="66"><circle cx="33" cy="33" r="32" fill="#2b6cb3"/><circle cx="33" cy="33" r="28" fill="none" stroke="#fff" stroke-width="1"/><circle cx="25" cy="40" r="5" fill="#fff"/><circle cx="42" cy="40" r="5" fill="#fff"/><rect x="22" y="24" width="18" height="12" fill="#fff"/></svg><div><h4>Equipment Financing</h4><p>Sed a pulvinar sapien. Aenean eleifend eget velit quis malesuada.</p></div></div>

<div class="abs loan" style="left:148px;top:2069px"><svg width="66" height="66"><circle cx="33" cy="33" r="32" fill="#2b6cb3"/><circle cx="33" cy="33" r="28" fill="none" stroke="#fff" stroke-width="1"/><rect x="24" y="18" width="18" height="30" fill="#fff"/><path d="M28 23h3M35 23h3M28 29h3M35 29h3M28 35h3M35 35h3" stroke="#2b6cb3" stroke-width="2"/></svg><div><h4>Commercial Real Estate</h4><p>Sed a pulvinar sapien. Aenean eleifend eget velit quis malesuada.</p></div></div>
<div class="abs loan" style="left:460px;top:2069px"><svg width="66" height="66"><circle cx="33" cy="33" r="32" fill="#2b6cb3"/><circle cx="33" cy="33" r="28" fill="none" stroke="#fff" stroke-width="1"/><path d="M16 30l10-6 7 5 7-5 10 6-10 10-7-4-7 4z" fill="#fff"/></svg><div><h4>Business Acquisitions</h4><p>Sed a pulvinar sapien. Aenean eleifend eget velit quis malesuada.</p></div></div>
<div class="abs loan" style="left:773px;top:2069px"><svg width="66" height="66"><circle cx="33" cy="33" r="32" fill="#2b6cb3"/><circle cx="33" cy="33" r="28" fill="none" stroke="#fff" stroke-width="1"/><circle cx="33" cy="33" r="5" fill="#fff"/><path d="M33 18v8M33 40v8M18 33h8M40 33h8M22 22l6 6M38 38l6 6M44 22l-6 6M22 44l6-6" stroke="#fff" stroke-width="2"/></svg><div><h4>Business Expansion</h4><p>Sed a pulvinar sapien. Aenean eleifend eget velit quis malesuada.</p></div></div>

<section class="abs contact" role="img" aria-label="Silhouettes of climbers helping each other up a rock face"></section>
<h2 class="abs section-title contact-title">CONTACT US</h2>
<div class="abs contact-brand">Corvane<small>Lending Partners</small></div>
<div class="abs info" style="top:2466px"><svg width="14" height="18" viewBox="0 0 14 20"><path d="M7 0a7 7 0 0 1 7 7c0 5-7 13-7 13S0 12 0 7a7 7 0 0 1 7-7z" fill="#fff"/><circle cx="7" cy="7" r="2.5" fill="#333"/></svg><div><b>CORVANE LENDING PARTNERS</b><span style="display:block;margin-top:6px">123 Lorem Ipsum Dolor, Sit Amet, Consectetur Adipisc - 12345</span></div></div>
<div class="abs info" style="top:2526px"><svg width="16" height="12" viewBox="0 0 24 18"><rect x="1" y="1" width="22" height="16" fill="#fff"/><path d="M1 1l11 9 11-9" stroke="#333" stroke-width="2" fill="none"/></svg><span>inquiry@corvanelending.com</span></div>
<div class="abs info" style="top:2560px"><svg width="14" height="14" viewBox="0 0 24 24"><path d="M6 2l4 4-2 3c1 3 4 6 7 7l3-2 4 4-3 4C10 22 2 14 2 5z" fill="#fff"/></svg><span>(00) 123 456 7890</span></div>

<div class="abs field" style="top:2352px">Name</div>
<div class="abs field" style="top:2392px">Email</div>
<div class="abs field" style="top:2433px;display:flex;justify-content:space-between">Inquiry For<svg width="10" height="16"><path d="M1 6l4 4 4-4" stroke="#ddd" fill="none"/></svg></div>
<div class="abs field" style="top:2475px;height:58px">Your Message</div>
<div class="abs submit">SUBMIT</div>

<div class="abs map" role="img" aria-label="Street map showing the office location"></div>
<div class="abs map-tag">CORVANE</div>
<svg class="abs" style="left:563px;top:2709px" width="24" height="34" viewBox="0 0 14 20"><path d="M7 0a7 7 0 0 1 7 7c0 5-7 13-7 13S0 12 0 7a7 7 0 0 1 7-7z" fill="#2b6cb3"/><circle cx="7" cy="7" r="2.5" fill="#fff"/></svg>

<footer class="abs footer">
  <span>Copyright © 2018 CORVANE LENDING PARTNERS. All Rights Reserved.</span>
  <i class="social" style="left:943px"></i>
  <i class="social" style="left:973px"></i>
  <i class="social" style="left:1003px"></i>
  <i class="social" style="left:1034px"></i>
</footer>

</body>
</html>
```